Business Card- Can you make it cool vs boring!

Need a refresh on my business card! Want it to be modern but simple, classic and a pop of coolness! we do senior living and it is boring. but that doesn't mean our business card have to look boring! Open to two sided cards. our website is www.Dunmere-PK.com

Target Market(s)

capital market

Industry/Entity Type

senior housing/ real estate

Contact Information for Business Card

logo/ name/ cell/ address/ www.Dunmere-PK.com/ space for a QR code

Requirements
Must have
• maybe a QR code (do not make prominent I may not use the QR so design where it can be taken out) that link to more about us/ landing page. needs to be modern but clean
Should not have
• clip art or script

```html
<!DOCTYPE html>
<html lang="en">
<head>
<meta charset="utf-8">
<title>Dunmere Living – Business Card</title>
<link rel="stylesheet" href="https://fonts.googleapis.com/css2?family=Poppins:wght@400;500;600&display=swap">
<style>
  :root {
    --page-bg: #e9e6e3;
    --wine-deep: #571108;
    --wine-mid: #7a2412;
    --wine-warm: #8c3218;
    --frost-top: #f4f7fb;
    --frost-mid: #eef1f4;
    --frost-blush: #f1dcdc;
    --arc-grey: #6e6866;
    --brand-red: #8a3626;
    --text-light: #ecdcd2;
    --text-soft: #dcc6ba;
    --icon-fill: #d9c1b4;
  }
  * { margin: 0; padding: 0; box-sizing: border-box; }
  html, body {
    width: 1200px;
    height: 970px;
    overflow: hidden;
    background: var(--page-bg);
    font-family: "Poppins", sans-serif;
  }
  .canvas {
    position: relative;
    width: 1200px;
    height: 970px;
  }
  .business-card {
    position: absolute;
    left: 60px;
    top: 177px;
    width: 1080px;
    height: 617px;
    overflow: hidden;
    box-shadow: 0 18px 40px rgba(60, 30, 20, 0.22);
  }
  .card-backdrop {
    position: absolute;
    inset: 0;
    width: 100%;
    height: 100%;
  }
  .brand-name {
    position: absolute;
    left: 0;
    width: 560px;
    top: 262px;
    text-align: center;
    font-weight: 500;
    font-size: 46px;
    letter-spacing: 1px;
    color: var(--brand-red);
  }
  .contact-block {
    position: absolute;
    left: 625px;
    top: 126px;
    color: var(--text-light);
  }
  .person-name {
    font-weight: 600;
    font-size: 33px;
    line-height: 1.1;
  }
  .person-title {
    font-size: 20px;
    color: var(--text-soft);
    margin-top: 2px;
  }
  .office-address {
    margin-top: 30px;
    font-size: 24px;
    line-height: 1.4;
  }
  .contact-list {
    list-style: none;
    margin-top: 18px;
  }
  .contact-item {
    display: flex;
    align-items: center;
    gap: 16px;
    font-size: 25px;
    line-height: 36px;
    color: var(--text-light);
  }
  .contact-icon {
    width: 30px;
    height: 30px;
    flex: none;
  }
  .social-row {
    display: flex;
    gap: 8px;
    margin-top: 36px;
  }
  .social-square {
    width: 37px;
    height: 37px;
    border-radius: 4px;
    background: var(--icon-fill);
    opacity: 0.75;
  }
</style>
</head>
<body>
<main class="canvas">
  <section class="business-card" aria-label="Dunmere Living business card">
    <svg class="card-backdrop" viewBox="0 0 1180 674" preserveAspectRatio="none" aria-hidden="true">
      <defs>
        <linearGradient id="wine-panel" x1="0" y1="0" x2="1" y2="1">
          <stop offset="0" stop-color="var(--wine-deep)"/>
          <stop offset="0.55" stop-color="var(--wine-mid)"/>
          <stop offset="1" stop-color="var(--wine-warm)"/>
        </linearGradient>
        <linearGradient id="frost-panel" x1="0" y1="0" x2="0" y2="1">
          <stop offset="0" stop-color="var(--frost-top)"/>
          <stop offset="0.6" stop-color="var(--frost-mid)"/>
          <stop offset="1" stop-color="var(--frost-blush)"/>
        </linearGradient>
      </defs>
      <rect class="wine-field" width="1180" height="674" fill="url(#wine-panel)"/>
      <circle class="accent-arc" cx="178" cy="250" r="470" fill="var(--arc-grey)"/>
      <circle class="frost-disc" cx="161" cy="257" r="462" fill="url(#frost-panel)"/>
    </svg>

    <div class="brand-name">Dunmere Living</div>

    <div class="contact-block">
      <h1 class="person-name">Nolan R Hayes</h1>
      <p class="person-title">CEO</p>
      <p class="office-address">4471 Birchfield Road<br>Suite #1408</p>
      <ul class="contact-list">
        <li class="contact-item">
          <svg class="contact-icon" viewBox="0 0 30 30" aria-hidden="true">
            <circle cx="15" cy="15" r="15" fill="var(--icon-fill)"/>
            <path d="M10.5 8.5l3 .5 1 3.5-2 1.3a8 8 0 0 0 3.7 3.7l1.3-2 3.5 1 .5 3-2 1.5c-5.5-.4-10-4.9-10.5-10.5z" fill="var(--wine-mid)"/>
          </svg>
          <span>(555) 310-48270</span>
        </li>
        <li class="contact-item">
          <svg class="contact-icon" viewBox="0 0 30 30" aria-hidden="true">
            <circle cx="15" cy="15" r="15" fill="var(--icon-fill)"/>
            <rect x="8" y="10" width="14" height="10" rx="1" fill="none" stroke="var(--wine-mid)" stroke-width="1.8"/>
            <path d="M8.5 10.5L15 16l6.5-5.5" fill="none" stroke="var(--wine-mid)" stroke-width="1.8"/>
          </svg>
          <span>hello@dunmeremail.com</span>
        </li>
        <li class="contact-item">
          <svg class="contact-icon" viewBox="0 0 30 30" aria-hidden="true">
            <circle cx="15" cy="15" r="15" fill="var(--icon-fill)"/>
            <circle cx="15" cy="15" r="7" fill="none" stroke="var(--wine-mid)" stroke-width="1.6"/>
            <ellipse cx="15" cy="15" rx="3" ry="7" fill="none" stroke="var(--wine-mid)" stroke-width="1.4"/>
            <path d="M8 15h14" stroke="var(--wine-mid)" stroke-width="1.4"/>
          </svg>
          <span>www.Dunmere-PK.com</span>
        </li>
      </ul>
      <div class="social-row" aria-label="Social profiles">
        <span class="social-square"></span>
        <span class="social-square"></span>
        <span class="social-square"></span>
      </div>
    </div>
  </section>
</main>
</body>
</html>
```